Four in One (Flexible infographic for Content Management Industry)

See attachment.
A graphic depicting 4 products, where each can stand on its own and each can be combined with others, but where, if all are taken together, the best result is achieved (the "super product").
Intended use is web. See attached file as an example.
The most basic idea is as the attached diagram shows, where 4 rectangles are arranged in a quadrangle, with a middle rectangle in the center representing the combined 4 products. This concept is fine except it is a bit too obvious as it stands. We are looking for either a variation of this or another concept.
The audience is technical + professional + enterprise - NOT consumers. Hence the design should be conservative in nature.
We are aware of tools like as Canva or Pictogram where such graphics are available, but we are looking for something with a bit more imagination and flexibility.
This graphic should be targeted to web sites and be delivered with vector-based (SVG) graphics.

```html
<!DOCTYPE html>
<html lang="en">
<head>
<meta charset="utf-8">
<title>Super Product – Four in One</title>
<link rel="stylesheet" href="https://fonts.googleapis.com/css2?family=Montserrat:wght@700&family=Roboto:wght@400;700&display=swap">
<style>
  :root {
    --bg: #d1d2d4;
    --card: #ffffff;
    --teal-light: #00a3bc;
    --teal-mid: #0b7e82;
    --teal-dark: #23453a;
    --title-green: #2db36b;
    --body-grey: #939598;
    --accent-red: #ed1c24;
    --dots: #b4b5b8;
  }
  html, body {
    margin: 0;
    padding: 0;
    width: 1200px;
    height: 847px;
    overflow: hidden;
    background: var(--bg);
  }
  .infographic {
    display: block;
    width: 1200px;
    height: 847px;
  }
  .card { fill: var(--card); }
  .hub-halo { fill: var(--card); stroke: var(--dots); stroke-width: 1.6; stroke-dasharray: 1.6 3.4; stroke-linecap: round; }
  .hub-ring { fill: url(#tealRing); }
  .hub-core { fill: var(--card); }
  .hub-label {
    font-family: "Montserrat", sans-serif;
    font-weight: 700;
    font-size: 52px;
    fill: var(--accent-red);
    text-anchor: middle;
  }
  .feature-title {
    font-family: "Roboto", sans-serif;
    font-weight: 700;
    font-size: 25px;
    fill: var(--title-green);
    text-anchor: middle;
  }
  .feature-text {
    font-family: "Roboto", sans-serif;
    font-weight: 400;
    font-size: 15.6px;
    fill: var(--body-grey);
    text-anchor: middle;
  }
  .icon { fill: url(#tealIcon); }
  .icon-glyph {
    font-family: "Roboto", sans-serif;
    font-weight: 700;
    font-size: 30px;
    fill: var(--card);
    text-anchor: middle;
  }
</style>
</head>
<body>
<svg class="infographic" viewBox="0 0 1200 847" xmlns="http://www.w3.org/2000/svg" role="img" aria-label="Four products combining into one super product">
  <defs>
    <linearGradient id="tealRing" x1="0" y1="0" x2="0" y2="1">
      <stop offset="0" stop-color="var(--teal-light)"/>
      <stop offset="0.45" stop-color="var(--teal-mid)"/>
      <stop offset="1" stop-color="var(--teal-dark)"/>
    </linearGradient>
    <linearGradient id="tealIcon" x1="0" y1="0" x2="0" y2="1">
      <stop offset="0" stop-color="var(--teal-light)"/>
      <stop offset="1" stop-color="var(--teal-dark)"/>
    </linearGradient>
    <filter id="ringShadow" x="-10%" y="-10%" width="120%" height="130%">
      <feDropShadow dx="0" dy="6" stdDeviation="7" flood-color="#000" flood-opacity="0.22"/>
    </filter>
    <path id="cardShape" d="M154,72 H558 Q586,72 586,100 V172 C586,205 582,228 574,250 L470,330 L386,392 C378,394 372,394 362,394 H154 Q126,394 126,366 V100 Q126,72 154,72 Z"/>
  </defs>

  <!-- cards -->
  <g class="cards">
    <use href="#cardShape" class="card"/>
    <use href="#cardShape" class="card" transform="translate(1223,0) scale(-1,1)"/>
    <use href="#cardShape" class="card" transform="translate(0,829) scale(1,-1)"/>
    <use href="#cardShape" class="card" transform="translate(1223,829) scale(-1,-1)"/>
  </g>

  <!-- central hub -->
  <g class="hub">
    <rect class="hub-halo" x="383" y="241" width="457" height="338" rx="205" ry="169"/>
    <rect class="hub-ring" x="395" y="253" width="434" height="314" rx="195" ry="157" filter="url(#ringShadow)"/>
    <rect class="hub-core" x="419" y="277" width="386" height="266" rx="172" ry="133"/>
    <text class="hub-label" x="607" y="393">SUPER</text>
    <text class="hub-label" x="607" y="450">PRODUCT</text>
  </g>

  <!-- feature: finance -->
  <g class="feature feature--finance">
    <circle class="icon" cx="316" cy="135" r="21"/>
    <text class="icon-glyph" x="316" y="146">$</text>
    <text class="feature-title" x="314" y="192">TITLE GOES HERE</text>
    <text class="feature-text" x="309" y="226">
      <tspan x="309">Lorem ipsum dolor sit amet,</tspan>
      <tspan x="309" dy="18.9">consectetuer dolore  adipiscing elit,</tspan>
      <tspan x="309" dy="18.9">sed diam nonummy nibh euismod</tspan>
      <tspan x="309" dy="18.9">tincidunt ut laoreet dolore magna</tspan>
      <tspan x="309" dy="18.9">aliquam.</tspan>
    </text>
  </g>

  <!-- feature: home -->
  <g class="feature feature--home">
    <path class="icon" d="M899,133 L915,117 L931,133 Z M902,135 H928 V152 H920 V144 a5,5 0 0 0 -10,0 V152 H902 Z"/>
    <text class="feature-title" x="912" y="196">TITLE GOES HERE</text>
    <text class="feature-text" x="908" y="230">
      <tspan x="908">Lorem ipsum dolor sit amet,</tspan>
      <tspan x="908" dy="18.9">consectetuer dolore  adipiscing elit,</tspan>
      <tspan x="908" dy="18.9">sed diam nonummy nibh euismod</tspan>
      <tspan x="908" dy="18.9">tincidunt ut laoreet dolore magna</tspan>
      <tspan x="908" dy="18.9">aliquam.</tspan>
    </text>
  </g>

  <!-- feature: growth -->
  <g class="feature feature--growth">
    <g class="icon">
      <rect x="284" y="525" width="4" height="12"/>
      <rect x="292" y="513" width="4" height="24"/>
      <rect x="300" y="519" width="4" height="18"/>
      <rect x="308" y="507" width="4" height="30"/>
      <rect x="316" y="498" width="4" height="39"/>
    </g>
    <text class="feature-title" x="307" y="579">TITLE GOES HERE</text>
    <text class="feature-text" x="302" y="613">
      <tspan x="302">Lorem ipsum dolor sit amet,</tspan>
      <tspan x="302" dy="18.9">consectetuer dolore  adipiscing elit,</tspan>
      <tspan x="302" dy="18.9">sed diam nonummy nibh euismod</tspan>
      <tspan x="302" dy="18.9">tincidunt ut laoreet dolore magna</tspan>
      <tspan x="302" dy="18.9">aliquam.</tspan>
    </text>
  </g>

  <!-- feature: quality -->
  <g class="feature feature--quality">
    <path class="icon" d="M915,505 L919.4,517.9 L933.1,518.1 L922.1,526.3 L926.2,539.4 L915,531.5 L903.8,539.4 L907.9,526.3 L896.9,518.1 L910.6,517.9 Z"/>
    <text class="feature-title" x="912" y="579">TITLE GOES HERE</text>
    <text class="feature-text" x="908" y="613">
      <tspan x="908">Lorem ipsum dolor sit amet,</tspan>
      <tspan x="908" dy="18.9">consectetuer dolore  adipiscing elit,</tspan>
      <tspan x="908" dy="18.9">sed diam nonummy nibh euismod</tspan>
      <tspan x="908" dy="18.9">tincidunt ut laoreet dolore magna</tspan>
      <tspan x="908" dy="18.9">aliquam.</tspan>
    </text>
  </g>
</svg>
</body>
</html>
```